Luxury Wine Label for New Startup Winery

We need a wine label for our new winery startup. We have worked with a local designer but do not feel the resulting label / logo have the elevation required to present our brand as a luxury wine. Our winery is called "Quailbrook Vineyards" and we are focused on extremely high quality hand crafted artisan and estate wines from the Pacific Northwest.
We would like to see designs that utilize a tree line, or other imagery that represents the "Quailbrook" part of our company name. Another interesting feature could be wood grain.
A logo will be required based on your design so please design with this in mind:
This logo should be consistent with the wine bottle label design, and should be representative of our high end exclusive wine while giving a sense of place (Oregon/ Pacific Northwest.)
I will supply an image of the design we received from our local designer, PLEASE NOTE: in general we do like wood grain and tree line concepts but feel the execution was poorly done.
ATTN: Logo design should be suitable for use on: Bottles (Red wine/rose/white wine), Bussiness cards, vehicle signage, business signage, etc
P.S.:
If you have a design that is not outside the box we are still interested in seeing it.
Label is for a burgundy style bottle with a label height of 3.5 - 4" and a width of 3.5-4"
any label <= 4"x4" and >=3.5"x3.5" will be acceptable:
HOWEVER Width should be greater than or equal to height due to the bottle format
Target Market(s)
Wine enthusiasts with adequate discretionary budgets to afford $100 bottles of wine.
Industry/Entity Type
Wine / Winery
Requirements
Must have
- A sense of luxury, a feel of exclusivity, and a theme consistent with our product and brand name
Nice to have
- Tree line, wood grain or other wood themes. Serif fonts
Should not have
- anything cheesy, off topic, hard to read script fonts or anything that makes the label hard to read from a few feet away or too busy

```html
<!DOCTYPE html>
<html lang="en">
<head>
<meta charset="utf-8">
<title>Quailbrook Vineyards – Syrah Label</title>
<link rel="stylesheet" href="https://fonts.googleapis.com/css2?family=Rozha+One&family=Josefin+Sans:wght@300;400&display=swap">
<style>
  :root {
    --backdrop: #a7a7a7;
    --label-black: #0a0a0a;
    --panel-black: #121212;
    --gold: #d8c98a;
    --gold-deep: #a8955a;
    --gold-line: #c9b878;
    --grain-dark: #1a1810;
    --grain-gold: #8f8250;
    --emblem-tone: #6e6542;
    --text-light: #f3f0e6;
  }
  * { box-sizing: border-box; margin: 0; padding: 0; }
  html, body { width: 960px; height: 1200px; overflow: hidden; }
  body {
    background: var(--backdrop);
    position: relative;
    font-family: "Josefin Sans", sans-serif;
  }

  /* ---------- Wine label ---------- */
  .wine-label {
    position: absolute;
    left: 50px; top: 620px;
    width: 440px; height: 481px;
    background: var(--label-black);
    box-shadow: 0 2px 6px rgba(0,0,0,0.25);
  }
  .upper-panel {
    position: absolute;
    left: 6px; top: 7px; right: 6px; height: 348px;
    border: 1.5px solid var(--gold-line);
  }
  .upper-panel::after {
    content: "";
    position: absolute;
    inset: 3px;
    border: 1px solid var(--gold-deep);
    pointer-events: none;
  }
  .contour-field {
    position: absolute;
    inset: 5px;
    background: radial-gradient(ellipse at 45% 35%, #2b2b2b 0%, #181818 45%, #0d0d0d 100%);
  }
  .label-emblem {
    position: absolute;
    left: 180px; top: 98px;
    width: 80px; height: 80px;
    border-radius: 50%;
    background: var(--emblem-tone);
  }
  .brand-name {
    position: absolute;
    left: 0; right: 0; top: 192px;
    text-align: center;
    font-family: "Rozha One", serif;
    font-weight: 400;
    color: var(--gold);
    font-size: 36px;
    line-height: 36px;
    letter-spacing: 1px;
  }
  .brand-name .line-small {
    display: block;
    font-size: 26px;
    line-height: 30px;
    letter-spacing: 2px;
  }
  .region {
    position: absolute;
    left: 0; right: 0; top: 273px;
    text-align: center;
    font-weight: 300;
    font-size: 15px;
    letter-spacing: 0.5px;
    color: var(--gold);
  }
  .varietal-band {
    position: absolute;
    left: 6px; right: 6px; top: 365px; height: 112px;
    border: 1.5px solid var(--gold-line);
  }
  .wood-grain {
    position: absolute;
    inset: 3px;
    background:
      linear-gradient(100deg, var(--grain-dark) 0%, var(--grain-gold) 22%, #3a341d 45%, var(--grain-gold) 72%, var(--grain-dark) 100%);
  }
  .varietal-box {
    position: absolute;
    left: 111px; top: 19px;
    width: 209px; height: 83px;
    border: 1.5px solid var(--gold-deep);
    border-radius: 14px;
    background: var(--panel-black);
    text-align: center;
  }
  .varietal-name {
    font-family: "Rozha One", serif;
    color: var(--gold);
    font-size: 42px;
    line-height: 1;
    letter-spacing: 2px;
    padding-top: 18px;
  }
  .vintage-tag {
    position: absolute;
    left: 50%; bottom: -6px;
    transform: translateX(-50%);
    background: #1c1c1c;
    border: 1px solid #555;
    color: var(--text-light);
    font-size: 8.5px;
    padding: 2px 4px 1px;
    white-space: nowrap;
    letter-spacing: 0.3px;
  }

  /* ---------- Standalone brand mark ---------- */
  .brand-emblem {
    position: absolute;
    left: 693px; top: 770px;
    width: 100px; height: 100px;
    border-radius: 50%;
    background: var(--emblem-tone);
  }
  .brand-panel {
    position: absolute;
    left: 551px; top: 876px;
    width: 388px; height: 101px;
    background: var(--label-black);
    border: 1.5px solid var(--gold-deep);
    border-radius: 10px;
    text-align: center;
    padding-top: 12px;
  }
  .brand-panel-name {
    font-family: "Rozha One", serif;
    font-weight: 400;
    color: var(--gold);
    font-size: 44px;
    line-height: 42px;
    letter-spacing: 1px;
  }
  .brand-panel-name .line-small {
    display: block;
    font-size: 31px;
    line-height: 34px;
    letter-spacing: 2px;
  }
</style>
</head>
<body>
  <section class="wine-label">
    <div class="upper-panel">
      <div class="contour-field" role="img" aria-label="Dotted topographic contour line pattern in grey on black"></div>
    </div>
    <div class="label-emblem" role="img" aria-label="Brand emblem area"></div>
    <h1 class="brand-name">QUAILBROOK<span class="line-small">VINEYARDS</span></h1>
    <p class="region">WILLAMETTE VALLEY</p>
    <div class="varietal-band">
      <div class="wood-grain" role="img" aria-label="Gold wood grain texture on black"></div>
      <div class="varietal-box">
        <p class="varietal-name">SYRAH</p>
        <span class="vintage-tag">ESTATE | 2023 | GROWN</span>
      </div>
    </div>
  </section>

  <div class="brand-emblem" role="img" aria-label="Brand emblem area"></div>
  <div class="brand-panel">
    <p class="brand-panel-name">QUAILBROOK<span class="line-small">VINEYARDS</span></p>
  </div>
</body>
</html>
```